indépendant en tant que Massothérapeute et Préparateur Mental, j'ai besoin de ...

Massothérapeute et préparateur mental indépendant, je recherche une carte de visite sobre et dynamique, sans images liées au massage ou à la préparation mentale mais intégrant mon logo. Les couleurs que j'aime bien sont : Blanc, gris, anthracite, noir et jaune

Contact Information for Business Card

carte de préférence Horizontale
neutre qui puisse toucher le deux domaines Massothérapie et préparation mentale

Requirements
Must have
• mon projet doit intégrer au recto:
LOGO
Loïc Bardèze
078 513 26 48
info@loicbardeze.ch
et éventuellement www.loicbardeze.ch

et au verso les deux adresses:

Chemin des Ormilles 7B
1400 Yverdon-les-Bains

Route de la Gravière 9
1700 Fribourg

Should not have
• mon projet ne doit pas contenir d'image en liens avec le massage ni la préparation mentale.

```html
<!DOCTYPE html>
<html lang="fr">
<head>
<meta charset="utf-8">
<title>Loïc Bardèze – Cartes de visite</title>
<link href="https://fonts.googleapis.com/css2?family=Poppins:wght@400;500;600&display=swap" rel="stylesheet">
<style>
  :root {
    --bg: #3a3a3a;
    --white: #ffffff;
    --ink: #2b2b2b;
    --anthracite: #1e1e1e;
    --yellow: #f5b400;
    --photo-light: #ece9e6;
    --photo-mid: #c9c2bc;
  }
  * { margin: 0; padding: 0; box-sizing: border-box; }
  html, body { width: 1200px; height: 930px; overflow: hidden; }
  body {
    background: var(--bg);
    font-family: "Poppins", sans-serif;
    position: relative;
  }
  .card {
    position: absolute;
    top: 300px;
    width: 540px;
    height: 330px;
    border-radius: 22px;
    overflow: hidden;
    box-shadow: 0 10px 30px rgba(0,0,0,.45);
  }
  .card--front { left: 40px; }
  .card--back { left: 620px; background: var(--anthracite); }

  .photo-area {
    position: absolute; inset: 0;
    background: radial-gradient(ellipse at 55% 45%, var(--photo-mid) 0%, var(--photo-light) 70%);
  }

  .brand { position: absolute; color: var(--ink); }
  .brand__name {
    display: flex; align-items: center; gap: 10px;
    font-weight: 600; font-size: 30px; letter-spacing: .5px; line-height: 1;
  }
  .brand__dot { width: 14px; height: 14px; border-radius: 50%; background: var(--ink); }
  .brand__tagline {
    margin-top: 6px; margin-left: 24px;
    font-size: 10.5px; font-weight: 500; letter-spacing: .8px; text-transform: uppercase;
  }
  .card--front .brand { left: 110px; top: 140px; }
  .card--back .brand { left: 225px; top: 58px; }
  .card--back .brand__name { font-size: 26px; }

  .shape { position: absolute; inset: 0; }

  .contact {
    position: absolute; left: 34px; bottom: 24px;
    color: var(--white); font-size: 12.5px; line-height: 1.4;
  }
  .contact__name { color: var(--yellow); font-weight: 600; font-size: 18px; text-transform: uppercase; line-height: 1.15; }
  .contact__role { font-size: 13.5px; margin-bottom: 6px; }
  .contact__line { display: flex; align-items: center; gap: 8px; }
  .contact__line svg { width: 11px; height: 11px; flex: none; }
  .contact__address { margin-top: 5px; }
</style>
</head>
<body>

  <section class="card card--front">
    <div class="photo-area" role="img" aria-label="Photo douce et désaturée en arrière-plan, tons gris clair"></div>
    <div class="brand">
      <div class="brand__name"><span class="brand__dot"></span>Loïc Bardèze</div>
      <div class="brand__tagline">Massothérapeute / Préparateur Mental</div>
    </div>
  </section>

  <section class="card card--back">
    <svg class="shape" viewBox="0 0 540 330" preserveAspectRatio="none" aria-hidden="true">
      <path d="M150 0 C165 140 290 245 540 258 L540 0 Z" fill="#ffffff"/>
      <path d="M150 0 C165 140 290 245 540 258" fill="none" stroke="#f5b400" stroke-width="5"/>
    </svg>

    <div class="brand">
      <div class="brand__name"><span class="brand__dot"></span>Loïc Bardèze</div>
      <div class="brand__tagline">Massothérapeute / Préparateur Mental</div>
    </div>

    <div class="contact">
      <div class="contact__name">Loïc Bardèze</div>
      <div class="contact__role">Director</div>
      <div class="contact__line">
        <svg viewBox="0 0 24 24"><path fill="#f5b400" d="M6.6 10.8a15 15 0 0 0 6.6 6.6l2.2-2.2c.3-.3.7-.4 1-.2 1.1.4 2.3.6 3.6.6.6 0 1 .4 1 1V20c0 .6-.4 1-1 1A17 17 0 0 1 3 4c0-.6.4-1 1-1h3.5c.6 0 1 .4 1 1 0 1.3.2 2.5.6 3.6.1.3 0 .7-.2 1z"/></svg>
        078 513 26 48
      </div>
      <div class="contact__line">
        <svg viewBox="0 0 24 24"><rect x="2" y="5" width="20" height="14" rx="2" fill="none" stroke="#f5b400" stroke-width="2.5"/><path d="M3 6l9 7 9-7" fill="none" stroke="#f5b400" stroke-width="2.5"/></svg>
        info@loicbardeze.ch
      </div>
      <div class="contact__line">
        <svg viewBox="0 0 24 24"><circle cx="12" cy="12" r="9" fill="none" stroke="#f5b400" stroke-width="2.5"/><path d="M3 12h18M12 3c3 3 3 15 0 18M12 3c-3 3-3 15 0 18" fill="none" stroke="#f5b400" stroke-width="2"/></svg>
        www.loicbardeze.ch
      </div>
      <div class="contact__address">Chemin des Ormilles 7B<br>1400 Yverdon-les-Bains</div>
      <div class="contact__address">Route de la Gravière 9<br>1700 Fribourg</div>
    </div>
  </section>

</body>
</html>
```